MARKETING MY MEDICAL PRACTICE

I am a physician providing medical-legal evaluations for competing attorneys (applicant attorneys representing injured workers versus defense attorneys and health insurance companies representing employers). Each opposing side wants me to be more biased toward their side. I am looking for a classy/elegant graphic design to apply to an exhibit booth LED backlit display, website, and printed brochures/business cards. I like the basic feel of the uploaded files IMG 1842 and IMG 1837. My medical practice focuses on evaluating patients with nerve, muscle, and skeletal injuries. I would like to include the three football players representing the nervous, muscular, and skeletal systems as well as the tools of my trade (goniometer measuring the knee range of motion, reflex hammer, and stethoscope with judge's gavel and hammer to describe what I do). I would like the goniometer, reflex hammer, and gavel & hammer to be faded into the back ground. The football players should be less opaque and more obvious.
I want my name in large big bold letters across the top of the graphics design: GERALD P. HOLLIS, M.D.
In smaller font below my name please place: Physical Medicine
One of the pics of me should be (with the backgrounds eliminated) on the side of my name (next to GERALD, not next to M.D.). I am not sure which pic would be better or more professionally appropriate.
On the other side of my name should be the illustration of the man showing muscular, skeletal, and nervous systems. It's my logo. I will supply the actual vector file of this logo once I receive it.
Somewhere in the graphics include: QME, AME, IME, & SIBTF evaluation
Somewhere in the graphics include: Physical Medicine: The specialty for neurological and musculoskeletal injuries in one evaluation by one doctor
Attorneys who refer injured workers for evaluation
MEDICAL SERVICES

```html
<!DOCTYPE html>
<html lang="en">
<head>
<meta charset="UTF-8">
<title>Gerald P. Hollis, M.D. — Physical Medicine</title>
<link href="https://fonts.googleapis.com/css2?family=Oswald:wght@500;600;700&family=Roboto:wght@400;500;700&display=swap" rel="stylesheet">
<style>
  :root {
    --page-bg: #e6e6e6;
    --red-light: #c1232e;
    --red-dark: #861520;
    --navy: #12141f;
    --navy-mid: #1c2236;
    --gold: #f3b23c;
    --white: #ffffff;
    --glow-blue: #2f5fd0;
    --glow-red: #b8343c;
  }
  * { box-sizing: border-box; margin: 0; padding: 0; }
  html, body {
    width: 800px; height: 1200px; overflow: hidden;
    background: var(--page-bg);
    font-family: "Roboto", Arial, sans-serif;
  }
  .banner {
    position: absolute; left: 20px; top: 315px;
    width: 760px; height: 570px; overflow: hidden;
    background: var(--navy);
    box-shadow: 0 4px 14px rgba(0,0,0,.25);
  }
  .banner__top {
    position: absolute; left: 0; top: 0; width: 100%; height: 330px;
    background: radial-gradient(ellipse at 45% 30%, var(--red-light), var(--red-dark) 80%);
  }
  .banner__bottom {
    position: absolute; left: 0; top: 330px; width: 100%; height: 240px;
    background: linear-gradient(180deg, var(--navy-mid), var(--navy));
  }
  .doctor-name {
    position: absolute; left: 0; width: 640px; top: 18px;
    text-align: center; color: var(--white);
    font-family: "Oswald", sans-serif; font-weight: 600;
    font-size: 54px; letter-spacing: 1px; line-height: 1;
  }
  .name-rule {
    position: absolute; left: 175px; width: 290px; top: 84px;
    height: 2px; background: var(--gold);
  }
  .specialty {
    position: absolute; left: 0; width: 640px; top: 90px;
    text-align: center; color: var(--gold);
    font-family: "Oswald", sans-serif; font-weight: 600;
    font-size: 30px; letter-spacing: 1px;
  }
  .tagline {
    position: absolute; left: 0; width: 640px; top: 138px;
    text-align: center; color: var(--white);
    font-size: 18px; font-weight: 500; line-height: 1.25;
  }
  .services {
    position: absolute; left: 265px; top: 196px;
    display: grid; grid-template-columns: 130px 2px 150px; column-gap: 26px; row-gap: 8px;
    color: var(--gold);
    font-family: "Oswald", sans-serif; font-weight: 600; font-size: 32px; line-height: 1;
  }
  .services__divider { grid-column: 2; grid-row: 1 / span 2; background: var(--gold); }
  .service { display: flex; align-items: flex-start; gap: 10px; }
  .service svg { width: 28px; height: 28px; flex: none; margin-top: 3px; }
  .service__note { display: block; font-size: 11px; font-weight: 500; letter-spacing: 1px; margin-top: 2px; }
  .placeholder { position: absolute; }
  .anatomy-figure {
    left: 648px; top: 40px; width: 92px; height: 300px; border-radius: 46px 46px 20px 20px;
    background: linear-gradient(180deg, #e3a87f, #b8453e 55%, #8f2b2b);
  }
  .doctor-photo {
    left: 40px; top: 190px; width: 215px; height: 380px;
    border-radius: 100px 100px 0 0;
    background: linear-gradient(180deg, #4b7cc0, #2c5c9c 60%, #22467a);
  }
  .player { top: 350px; width: 105px; height: 205px; border-radius: 50px 50px 24px 24px; }
  .player--nerve { left: 290px; background: radial-gradient(ellipse, #5d86e8, var(--glow-blue) 55%, transparent 75%); }
  .player--muscle { left: 425px; background: radial-gradient(ellipse, #d8646a, var(--glow-red) 50%, #3b3f80 70%, transparent 78%); }
  .player--skeleton { left: 560px; background: radial-gradient(ellipse, #6a93ef, var(--glow-blue) 55%, transparent 75%); }
  .name-tag {
    position: absolute; left: 14px; top: 496px; width: 250px; height: 56px;
    background: var(--navy); border: 2px solid var(--red-light); border-radius: 10px;
    display: flex; align-items: center; gap: 10px; padding: 0 12px;
  }
  .name-tag__mark { width: 14px; height: 14px; background: var(--gold); flex: none; }
  .name-tag__name {
    color: var(--white); font-family: "Oswald", sans-serif; font-weight: 600; font-size: 16px; line-height: 1.1;
  }
  .name-tag__role { display: block; color: var(--gold); font-family: "Roboto", sans-serif; font-weight: 500; font-size: 10px; }
</style>
</head>
<body>
  <section class="banner">
    <div class="banner__top"></div>
    <div class="banner__bottom"></div>

    <h1 class="doctor-name">GERALD P. HOLLIS, M.D.</h1>
    <div class="name-rule"></div>
    <h2 class="specialty">PHYSICAL MEDICINE</h2>
    <p class="tagline">The specialty for neurological and musculoskeletal<br>injuries in one evaluation by one doctor</p>

    <div class="services">
      <div class="service" style="grid-column:1;grid-row:1">
        <svg viewBox="0 0 28 28"><rect x="2" y="6" width="20" height="20" fill="none" stroke="currentColor" stroke-width="2.5"/><path d="M6 15l5 5L26 3" fill="none" stroke="currentColor" stroke-width="3"/></svg>QME
      </div>
      <div class="service" style="grid-column:1;grid-row:2">
        <svg viewBox="0 0 28 28"><rect x="2" y="6" width="20" height="20" fill="none" stroke="currentColor" stroke-width="2.5"/><path d="M6 15l5 5L26 3" fill="none" stroke="currentColor" stroke-width="3"/></svg>AME
      </div>
      <div class="services__divider"></div>
      <div class="service" style="grid-column:3;grid-row:1">
        <svg viewBox="0 0 28 28"><rect x="2" y="6" width="20" height="20" fill="none" stroke="currentColor" stroke-width="2.5"/><path d="M6 15l5 5L26 3" fill="none" stroke="currentColor" stroke-width="3"/></svg>IME
      </div>
      <div class="service" style="grid-column:3;grid-row:2">
        <svg viewBox="0 0 28 28"><rect x="2" y="6" width="20" height="20" fill="none" stroke="currentColor" stroke-width="2.5"/><path d="M6 15l5 5L26 3" fill="none" stroke="currentColor" stroke-width="3"/></svg>
        <span>SIBTF<span class="service__note">EVALUATION</span></span>
      </div>
    </div>

    <div class="placeholder anatomy-figure" role="img" aria-label="Anatomical figure showing muscular, skeletal and nervous systems"></div>
    <div class="placeholder player player--nerve" role="img" aria-label="Football player figure showing the nervous system"></div>
    <div class="placeholder player player--muscle" role="img" aria-label="Football player figure showing the muscular system"></div>
    <div class="placeholder player player--skeleton" role="img" aria-label="Football player figure showing the skeletal system"></div>
    <div class="placeholder doctor-photo" role="img" aria-label="Photo of the doctor in a blue polo shirt, arms crossed"></div>

    <div class="name-tag">
      <span class="name-tag__mark"></span>
      <p class="name-tag__name">GERALD P. HOLLIS, M.D.<span class="name-tag__role">Physical Medicine &amp; Rehabilitation</span></p>
    </div>
  </section>
</body>
</html>
```